Seeking a new website design for electrical contracting company

Brisket & Vane electrical contracting needs a new website for brisket-vane.example

We are looking for modern and something real cool with motion for a landing page. we have some cool images from our photo shoot. maybe even 3d motion our existing logo. we would like something we can edit with news and events and update a past project page. Also allow to take payment
stock images at
https://lorapellwinphotos.picvault-demo.example/Brisket-and-Vane

Target Market(s)

construction , home owners , business owners,

Industry/Entity Type

construction , electrical

Coding

Number of Pages Required

5+ page

Font styles to use
Serif
Sans Serif

Colors
0054AA
0677BA
7BADD7
CADEEF
E8F1F8
0094D4
00A9DD
6FCCEA
C7EBF8
E9F6FB
FFF300
FFF600
FEFA6F
FFFEC7
FFFEE8

Requirements
Must have
• excitement, motion, selling professionalism,

```html
<!DOCTYPE html>
<html lang="en">
<head>
<meta charset="utf-8">
<title>Brisket &amp; Vane — Electrical Contractors</title>
<link href="https://fonts.googleapis.com/css2?family=Montserrat:wght@400;500;600;700&display=swap" rel="stylesheet">
<style>
:root{
  --navy:#233a7e;
  --yellow:#ffe600;
  --ink:#111111;
  --dark:#2a2a2a;
  --grey-band:#efefef;
  --muted:#8a8a8a;
  --white:#ffffff;
}
*{box-sizing:border-box;margin:0;padding:0}
html,body{width:1200px;height:4057px;overflow:hidden}
body{position:relative;font-family:"Montserrat",Arial,sans-serif;color:var(--ink);background:var(--white)}
.abs{position:absolute}
.btn{position:absolute;background:var(--yellow);color:var(--ink);font-weight:600;font-size:15px;display:flex;align-items:center;justify-content:center;border-radius:3px}
.eyebrow{font-size:17px;font-weight:500;letter-spacing:.5px;color:var(--muted);text-transform:uppercase}
.h2{font-size:42px;font-weight:700;color:var(--navy);line-height:1.15}
.center{left:0;width:1200px;text-align:center}
.photo{position:absolute;overflow:hidden}
/* header */
.brand{position:absolute;display:flex;align-items:center;gap:10px;font-weight:700;font-size:22px;color:var(--navy)}
.brand .mark{width:30px;height:30px;background:var(--navy)}
.nav{position:absolute;left:474px;top:42px;display:flex;gap:21px;font-size:14px;font-weight:500}
.phone{position:absolute;background:var(--yellow);border-radius:4px;display:flex;align-items:center;gap:8px;justify-content:center;font-size:15px;font-weight:600}
/* hero */
.hero{left:0;top:107px;width:1200px;height:485px;background:#0e1838}
.hero-photo{left:520px;top:107px;width:680px;height:485px;
  background:
    radial-gradient(ellipse 160px 200px at 62% 62%,#e0701f 0%,rgba(224,112,31,.6) 45%,rgba(224,112,31,0) 100%),
    radial-gradient(ellipse 140px 120px at 66% 22%,#c9a487 0%,rgba(201,164,135,0) 100%),
    linear-gradient(90deg,#0e1838 0%,#1d2744 22%,#4a4f5c 48%,#8d8f93 78%,#cfd0d2 100%)}
.hero-text{left:75px;top:220px;color:var(--white)}
.hero-text .eyebrow{color:#e6e6e6;font-size:18px}
.hero-text h1{font-size:44px;line-height:1.12;font-weight:600;margin-top:6px}
.hero-text p{font-size:14px;line-height:1.45;margin-top:18px;width:430px}
.feature{position:absolute;top:562px;width:306px;height:173px;background:var(--dark);color:var(--white);border-radius:3px;padding:26px 22px}
.feature.yellow{background:var(--yellow);color:var(--ink)}
.feature .title{display:flex;align-items:center;gap:14px;font-size:19px;font-weight:600;color:var(--yellow)}
.feature.yellow .title{color:var(--ink)}
.feature .ico{width:48px;height:48px;border-radius:50%;background:var(--white);display:flex;align-items:center;justify-content:center}
.feature p{font-size:13px;line-height:1.45;margin-top:18px}
/* about */
.about-text{left:696px;top:842px;width:430px}
.about-text p{font-size:13.5px;line-height:1.45;margin-top:14px}
/* services */
.band{left:0;top:1255px;width:1200px;height:639px;background:var(--grey-band)}
.tab{position:absolute;top:1408px;height:34px;background:var(--white);font-size:15px;font-weight:600;display:flex;align-items:center;justify-content:center;border-radius:3px}
.tab.active{background:var(--yellow)}
.svc{position:absolute;top:1475px;width:325px;height:342px;overflow:hidden}
.svc .label{position:absolute;left:22px;bottom:38px;display:flex;align-items:center;gap:14px;color:var(--white);font-weight:600;font-size:17px}
.svc-card{position:absolute;left:30px;bottom:20px;width:265px;height:120px;background:var(--white);border-radius:8px;padding:22px 18px 0 90px}
.svc-card b{font-size:16px;color:var(--navy);font-weight:600}
.svc-card p{font-size:12px;line-height:1.4;margin-top:10px;color:#333}
.dot{position:absolute;top:1855px;width:34px;height:4px;background:var(--ink)}
/* projects */
.proj-card{position:absolute;left:93px;top:2480px;width:290px;height:84px;background:var(--white);border-radius:8px;padding:12px 14px}
.proj-card b{display:block;font-size:24px;color:var(--navy);font-weight:600}
.proj-card span{font-size:17px}
/* why */
.why{left:0;top:2715px;width:1200px;height:530px;background:linear-gradient(90deg,#3a3a3a 40%,#4a4a4a 70%,#555 100%)}
.why-text{left:592px;top:2785px;color:var(--white)}
.why-text .eyebrow{color:#d0d0d0}
.why-text h2{font-size:42px;font-weight:600;line-height:1.18;margin-top:6px}
.perk{position:absolute;display:flex;align-items:center;gap:16px;color:var(--white);font-size:21px;font-weight:500;line-height:1.25}
.perk .ico{width:76px;height:76px;border-radius:50%;background:var(--ink);display:flex;align-items:center;justify-content:center;flex:none}
/* contact */
.contact-box{left:563px;top:3355px;width:562px;height:451px;background:var(--yellow);border-radius:4px}
.field{position:absolute;background:var(--white);border-radius:3px;font-size:11px;color:#888;padding:9px 12px}
.submit{position:absolute;left:629px;top:3727px;width:430px;height:32px;background:var(--ink);color:var(--white);font-weight:600;font-size:15px;display:flex;align-items:center;justify-content:center;border-radius:3px}
/* footer */
.footer{left:0;top:3917px;width:1200px;height:140px;background:#141414}
.fnav{position:absolute;left:378px;top:3962px;display:flex;gap:20px;color:var(--white);font-size:14px}
.fnav span::before{content:"";display:inline-block;width:7px;height:7px;border-radius:50%;background:var(--yellow);margin-right:6px;vertical-align:middle}
.legal{position:absolute;top:4026px;font-size:12px;color:var(--white)}
</style>
</head>
<body>

<!-- Header -->
<div class="brand" style="left:75px;top:36px"><span class="mark"></span>Brisket &amp; Vane</div>
<nav class="nav"><span>About Us</span><span>Our Services</span><span>Projects</span><span>Testimonials</span><span>Contact Us</span></nav>
<div class="phone" style="left:967px;top:36px;width:158px;height:34px">
  <svg width="16" height="16" viewBox="0 0 24 24"><circle cx="12" cy="12" r="12" fill="#111"/><path d="M8 6l2 0 1 3-1.5 1a7 7 0 003.5 3.5l1-1.5 3 1 0 2a2 2 0 01-2 2A10 10 0 016 8a2 2 0 012-2z" fill="#ffe600"/></svg>
  (555)014-2290</div>

<!-- Hero -->
<div class="abs hero"></div>
<div class="photo hero-photo" role="img" aria-label="Smiling electrician in white hard hat and orange safety vest holding a tablet beside a switchboard"></div>
<div class="abs hero-text">
  <div class="eyebrow">Welcome to Brisket &amp; Vane</div>
  <h1>Powering Your World,<br>Safely and Efficiently</h1>
  <p>Lorem ipsum dolor sit amet, consectetur adipiscing elit, sed do eiusmod tempor incididunt ut labore.</p>
</div>
<div class="btn" style="left:75px;top:406px;width:213px;height:34px">Get a Free Quote</div>

<div class="feature" style="left:100px">
  <div class="title"><span class="ico"><svg width="24" height="24" viewBox="0 0 24 24"><circle cx="12" cy="12" r="8" fill="none" stroke="#111" stroke-width="2"/><path d="M12 7v10M9 9.5h4.5a1.5 1.5 0 010 3h-3a1.5 1.5 0 000 3H15" stroke="#111" stroke-width="1.6" fill="none"/></svg></span>Affordable Price</div>
  <p>Lorem ipsum dolor sit amet, consectetur adipiscing elit, sed do eiusmod tempor incididunt ut.</p>
</div>
<div class="feature yellow" style="left:447px">
  <div class="title"><span class="ico"><svg width="24" height="24" viewBox="0 0 24 24"><circle cx="12" cy="12" r="9" fill="none" stroke="#111" stroke-width="2"/><path d="M12 7v5l3 2" stroke="#111" stroke-width="2" fill="none"/></svg></span>24/7 Our Service</div>
  <p>Lorem ipsum dolor sit amet, consectetur adipiscing elit, sed do eiusmod tempor incididunt ut.</p>
</div>
<div class="feature" style="left:793px">
  <div class="title"><span class="ico"><svg width="24" height="24" viewBox="0 0 24 24"><path d="M12 3l7 3v5c0 5-3 8-7 10-4-2-7-5-7-10V6z" fill="none" stroke="#111" stroke-width="2"/><path d="M8.5 12l2.5 2.5 4.5-5" stroke="#111" stroke-width="2" fill="none"/></svg></span>100% Guarantee</div>
  <p>Lorem ipsum dolor sit amet, consectetur adipiscing elit, sed do eiusmod tempor incididunt ut.</p>
</div>

<!-- About -->
<div class="photo" style="left:75px;top:811px;width:565px;height:369px;border-radius:4px;background:linear-gradient(180deg,#4a4a4a 0%,#e9eaec 18%,#d6d8da 42%,#60656b 58%,#3f4a5e 78%,#2f3640 100%)" role="img" aria-label="Five electricians with tool belts standing in front of white company vans"></div>
<div class="abs about-text">
  <div class="eyebrow">About Us</div>
  <div class="h2" style="margin-top:6px">Trusted Experts in Electrical Solutions</div>
  <p>Lorem ipsum dolor sit amet, consectetur adipiscing elit, sed do eiusmod tempor incididunt ut labore et dolore magna aliqua. Ut enim ad minim veniam, quis nostrud exercitation ullamco laboris nisi ut aliquip ex ea commodo consequat.</p>
  <p style="margin-top:10px">Lorem ipsum dolor sit amet, consectetur adipiscing elit, sed do eiusmod tempor incididunt ut labore.</p>
</div>
<div class="btn" style="left:696px;top:1123px;width:140px;height:32px">Read More</div>

<!-- Services -->
<div class="abs band"></div>
<div class="abs eyebrow center" style="top:1297px">Our Services</div>
<div class="abs h2 center" style="top:1318px">Reliable Services You Can Count On</div>
<div class="tab active" style="left:275px;width:194px">Residential Services</div>
<div class="tab" style="left:500px;width:200px">Commercial Services</div>
<div class="tab" style="left:726px;width:199px">Industrial Services</div>

<div class="svc" style="left:75px;background:linear-gradient(180deg,#cfcfcf 0%,#3a3c3e 25%,#2c2e30 45%,#9aa070 60%,#d9d7cf 78%,#e8d52a 100%)" role="img" aria-label="Gloved hand connecting colourful wires to outlet boxes">
  <div class="svc-card">
    <svg class="abs" style="left:14px;top:26px" width="60" height="60" viewBox="0 0 60 60" fill="none" stroke="#111" stroke-width="2"><rect x="6" y="10" width="20" height="40" rx="2"/><path d="M26 22h14M26 30h20M26 38h14"/><circle cx="46" cy="20" r="7"/></svg>
    <b>Home rewiring</b>
    <p>Lorem ipsum dolor sit amet, consectetur adipiscing elit,</p>
  </div>
</div>
<div class="svc" style="left:437px;background:radial-gradient(circle at 60% 38%,#f0b060 0%,#b8621c 25%,#6a3208 60%,#2a1204 100%)" role="img" aria-label="Gloved hand fitting a glowing light bulb">
  <div class="label"><svg width="44" height="48" viewBox="0 0 44 48" fill="none" stroke="#fff" stroke-width="2"><path d="M4 6h14v8H4zM18 10h8l4 10H12z"/><path d="M21 20v18"/><circle cx="21" cy="42" r="4"/></svg>Lighting installation</div>
</div>
<div class="svc" style="left:800px;background:linear-gradient(110deg,#2c3440 0%,#3a4250 40%,#7a7f86 70%,#4a4f56 100%)" role="img" aria-label="Electrician in hard hat working on an electrical panel">
  <div class="label"><svg width="52" height="52" viewBox="0 0 52 52" fill="none" stroke="#fff" stroke-width="2"><rect x="6" y="4" width="40" height="32" rx="2"/><path d="M26 10l-8 16h16z"/><path d="M26 36v10M12 46h28"/></svg>Electrical panel upgrades</div>
</div>
<div class="dot" style="left:523px;background:var(--yellow)"></div>
<div class="dot" style="left:563px"></div>
<div class="dot" style="left:603px"></div>
<div class="dot" style="left:643px"></div>

<!-- Projects -->
<div class="abs eyebrow center" style="top:1973px">Our Projects</div>
<div class="abs h2 center" style="top:1995px">Powering Success, One Project at a Time</div>
<div class="photo" style="left:75px;top:2076px;width:325px;height:497px;background:linear-gradient(90deg,#c9c6bf 0%,#e2dfd8 35%,#8a8780 65%,#4e4c48 100%)" role="img" aria-label="Hand pulling cables through a wall with a tool bag below"></div>
<div class="proj-card"><b>Voltline Works</b><span>Debris stuck in the outdoor</span></div>
<div class="photo" style="left:437px;top:2076px;width:325px;height:231px;background:linear-gradient(90deg,#2e3034 0%,#4a4c50 45%,#2c4f8c 75%,#d8d8d0 100%)" role="img" aria-label="Electrician in safety glasses stripping wires at a panel"></div>
<div class="photo" style="left:800px;top:2076px;width:325px;height:231px;background:linear-gradient(135deg,#b8632a 0%,#d89058 45%,#e6d8c8 70%,#c07038 100%)" role="img" aria-label="Hands wiring a ceiling light fitting"></div>
<div class="photo" style="left:437px;top:2342px;width:688px;height:231px;background:linear-gradient(90deg,#1c2432 0%,#26303f 55%,#a87838 72%,#4a5464 85%,#6a7484 100%)" role="img" aria-label="City buildings lit up at dusk seen from above"></div>
<div class="btn" style="left:493px;top:2606px;width:214px;height:34px">View All Projects</div>

<!-- Why choose us -->
<div class="abs why"></div>
<div class="photo" style="left:0;top:2715px;width:470px;height:530px;background:radial-gradient(ellipse 110px 90px at 28% 32%,#e8801e 0%,rgba(232,128,30,0) 100%),linear-gradient(90deg,#3c4048 0%,#7c8490 40%,#5a6c88 70%,#8c939c 100%)" role="img" aria-label="Electrician in orange hard hat testing a wired control cabinet"></div>
<div class="abs why-text">
  <div class="eyebrow">Why Choose Us?</div>
  <h2>Built on Trust. Powered<br>by Expertise.</h2>
</div>
<div class="perk" style="left:592px;top:2940px"><span class="ico"><svg width="38" height="38" viewBox="0 0 38 38" fill="none" stroke="#fff" stroke-width="2"><circle cx="19" cy="15" r="9"/><path d="M13 23l-3 11 9-4 9 4-3-11"/></svg></span>10+ Years<br>of Experience</div>
<div class="perk" style="left:893px;top:2940px"><span class="ico"><svg width="38" height="38" viewBox="0 0 38 38" fill="none" stroke="#fff" stroke-width="2"><rect x="5" y="8" width="28" height="22" rx="2"/><circle cx="13" cy="18" r="3"/><path d="M20 16h9M20 21h9M9 25h20"/></svg></span>Licensed &amp;<br>Insured</div>
<div class="perk" style="left:592px;top:3045px"><span class="ico"><svg width="38" height="38" viewBox="0 0 38 38" fill="none" stroke="#fff" stroke-width="2"><circle cx="19" cy="19" r="13"/><path d="M19 11v8l5 4"/></svg></span>24/7 Emergency<br>Services</div>
<div class="perk" style="left:893px;top:3045px"><span class="ico"><svg width="38" height="38" viewBox="0 0 38 38" fill="none" stroke="#fff" stroke-width="2"><path d="M19 4l13 6v8c0 8-6 13-13 16-7-3-13-8-13-16v-8z"/><path d="M19 12v14M15.5 15h5a2 2 0 010 4h-3a2 2 0 000 4h5"/></svg></span>Transparent<br>Pricing</div>
<div class="btn" style="left:592px;top:3146px;width:213px;height:34px">Get a Free Quote</div>

<!-- Contact -->
<div class="photo" style="left:75px;top:3322px;width:592px;height:520px;border-radius:4px;background:linear-gradient(180deg,#7a4a3a 0%,#9a6a56 12%,#e4e4e2 28%,#c8cacc 40%,#2e3440 55%,#2a3346 70%,#3c4a66 85%,#5a5a58 100%)" role="img" aria-label="Four electricians in company shirts standing in front of a work van"></div>
<div class="abs contact-box"></div>
<div class="abs" style="left:563px;top:3400px;width:562px;text-align:center">
  <div style="font-size:17px;font-weight:500">CONTACT US NOW</div>
  <div style="font-size:29px;font-weight:700;color:var(--navy);margin-top:4px">Need Electrical Help? Let’s Talk!</div>
</div>
<div class="field" style="left:629px;top:3490px;width:430px;height:30px">Enter Your Name*</div>
<div class="field" style="left:629px;top:3537px;width:430px;height:30px">Enter Your Phone Number*</div>
<div class="field" style="left:629px;top:3584px;width:206px;height:30px;display:flex;justify-content:space-between">-- Select Your Service --<svg width="12" height="12" viewBox="0 0 12 12"><path d="M2 4l4 4 4-4" stroke="#111" stroke-width="1.6" fill="none"/></svg></div>
<div class="field" style="left:853px;top:3584px;width:206px;height:30px">Enter Your Email*</div>
<div class="field" style="left:629px;top:3625px;width:430px;height:87px">Message*</div>
<div class="submit">Submit</div>

<!-- Footer -->
<div class="abs footer"></div>
<div class="brand" style="left:75px;top:3950px;color:#fff"><span class="mark" style="background:#fff"></span>Brisket &amp; Vane</div>
<div class="fnav"><span>About Us</span><span>Our Services</span><span>Projects</span><span>Testimonials</span><span>Contact Us</span></div>
<div class="phone" style="left:981px;top:3953px;width:144px;height:34px">
  <svg width="16" height="16" viewBox="0 0 24 24"><circle cx="12" cy="12" r="12" fill="#111"/><path d="M8 6l2 0 1 3-1.5 1a7 7 0 003.5 3.5l1-1.5 3 1 0 2a2 2 0 01-2 2A10 10 0 016 8a2 2 0 012-2z" fill="#ffe600"/></svg>
  (555)014-2290</div>
<div class="abs" style="left:0;top:4008px;width:1200px;height:1px;background:#3a3a3a"></div>
<div class="legal" style="left:75px">2025 © All rights Reserved.</div>
<div class="legal" style="left:925px">Privacy Policy &nbsp;|&nbsp; Term &amp; Conditions</div>

</body>
</html>
```